Kampfsport Außenwerbung
Zielgruppe
Kampfsportschule für Kinder, Jugendliche und Erwachsene. Sportarten: Kick-Boxen, Jiu-Jitsu und Tricking
Aufgabenstellung
Ich bräuchte für meine Schaufenster eine schöne Außenwerbung. Beworben werden sollen alle meine Sportarten. Ich lade meinen Flyer hoch, damit im ähnlichen Stil gearbeitet werden kann. Außerdem auch noch andere Beispiele an denen man sich orientieren kann, sowie mein Logo und meine Fensterfront.

```html
<!DOCTYPE html>
<html lang="de">
<head>
<meta charset="utf-8">
<title>Martial Arts Borq – Schaufensterbeklebung</title>
<link href="https://fonts.googleapis.com/css2?family=Alegreya+Sans:ital,wght@0,800;1,800&family=Montserrat:wght@500;700;800&display=swap" rel="stylesheet">
<style>
  :root{
    --bg:#efefee;
    --frame:#e4e6e8;
    --frame-edge:#c9ccd0;
    --glass:#d9d2ca;
    --glass-light:#ebe6e0;
    --black:#0e0e0f;
    --ink:#1a1a1c;
    --red:#e4262c;
    --coral:#f2654b;
    --white:#ffffff;
  }
  *{box-sizing:border-box;margin:0;padding:0}
  html,body{width:1200px;height:1200px;overflow:hidden;background:var(--bg)}
  body{position:relative;font-family:"Montserrat",sans-serif}

  .storefront{position:absolute;left:55px;top:225px;width:1090px;height:780px;background:var(--frame);border:3px solid var(--frame-edge)}
  .pane{position:absolute;overflow:hidden;background:linear-gradient(160deg,var(--glass-light),var(--glass));border:2px solid var(--frame-edge)}
  .pane svg.graphic{position:absolute;inset:0;width:100%;height:100%}

  .photo{position:absolute;border-radius:40% 40% 12% 12%}
  .photo--kick{background:linear-gradient(170deg,#c9302e 0%,#1c1c1e 35%,#26262a 70%,#c43a5c 100%)}
  .photo--trick{background:linear-gradient(180deg,#e9c7b2 0%,#1b1b1d 30%,#1b1b1d 80%,#e0b84a 100%)}
  .photo--jiu{background:linear-gradient(180deg,#d9b595 0%,#f4f4f4 22%,#eaeaea 60%,#e6c23a 62%,#f2f2f2 70%,#ededed 100%)}

  .brand{position:absolute;left:0;right:0;display:flex;justify-content:center;align-items:center;gap:6px;color:var(--white);font-weight:800;letter-spacing:.02em;white-space:nowrap}
  .brand__dot{display:inline-block;width:10px;height:10px;border-radius:50%;background:var(--red);flex:none}

  .rot{position:absolute;transform-origin:left top;white-space:nowrap;color:var(--white)}

  .headline{position:absolute;left:18px;top:16px;color:var(--white);font-family:"Alegreya Sans",sans-serif;font-weight:800;transform:rotate(-3deg);transform-origin:left top}
  .headline__main{font-size:22px;letter-spacing:.02em}
  .headline__sub{font-size:19px;font-style:italic;margin-left:14px;line-height:1.25}

  .label-kick{position:absolute;left:20px;bottom:60px;color:var(--white);font-family:"Alegreya Sans",sans-serif;font-style:italic;font-weight:800;line-height:1.05}
  .label-kick span{display:block}
  .label-kick .big{font-size:24px}
  .label-kick .small{font-size:17px}

  .contact-phone{left:22px;top:470px;transform:rotate(-49deg);font-weight:800;font-size:16px}
  .contact-mail{left:44px;top:488px;transform:rotate(-49deg);font-weight:700;font-size:10px}

  .schedule{position:absolute;left:8px;top:100px;width:170px;background:var(--frame);border-radius:4px;padding:4px}
  .schedule table{width:100%;border-collapse:collapse;font-size:4.6px;line-height:1.15;font-weight:500}
  .schedule th{background:var(--black);color:var(--white);font-weight:700;padding:2px 1px;font-size:4.2px}
  .schedule td{padding:1.5px 1px;border:.5px solid #999;background:var(--black);color:var(--white)}
  .schedule td.time{background:var(--white);color:var(--red);font-weight:700}
  .schedule td.jj{background:var(--red)}
  .schedule td.alt{background:#e3e3e3;color:var(--ink)}
  .schedule td.empty{background:#f3f3f3}
</style>
</head>
<body>
<main class="storefront">

  <!-- Oberlichter -->
  <div class="pane" style="left:10px;top:10px;width:115px;height:170px"></div>

  <div class="pane" style="left:135px;top:10px;width:135px;height:170px">
    <svg class="graphic" viewBox="0 0 135 170" preserveAspectRatio="none">
      <polygon points="135,20 135,170 15,170" fill="var(--black)"/>
      <polygon points="135,40 135,52 40,170 25,170" fill="var(--red)" opacity=".7"/>
    </svg>
  </div>

  <div class="pane" style="left:280px;top:10px;width:380px;height:170px">
    <svg class="graphic" viewBox="0 0 380 170" preserveAspectRatio="none">
      <polygon points="0,0 350,0 200,170 0,170" fill="var(--black)"/>
      <polygon points="0,112 330,85 320,100 0,140" fill="var(--red)"/>
      <polygon points="20,85 310,58 300,72 10,100" fill="var(--coral)"/>
      <polygon points="230,170 370,20 380,20 380,30 250,170" fill="var(--red)"/>
      <polygon points="330,0 380,0 380,12 320,80" fill="var(--black)"/>
    </svg>
    <div class="headline">
      <div class="headline__main">WIR MACHEN KINDER STARK</div>
      <div class="headline__sub">KAMPSPORT &amp;</div>
      <div class="headline__sub">SELBSTVERTEITIGUNG</div>
    </div>
  </div>

  <div class="pane" style="left:670px;top:10px;width:190px;height:170px">
    <svg class="graphic" viewBox="0 0 190 170" preserveAspectRatio="none">
      <polygon points="190,20 190,170 40,170" fill="var(--black)"/>
      <polygon points="70,70 190,40 190,58 60,86" fill="var(--red)"/>
      <polygon points="80,110 190,88 190,104 70,124" fill="var(--coral)"/>
    </svg>
  </div>

  <div class="pane" style="left:870px;top:10px;width:205px;height:170px;background:var(--black)">
    <svg class="graphic" viewBox="0 0 205 170" preserveAspectRatio="none">
      <polygon points="0,40 205,14 205,28 0,56" fill="var(--red)" opacity=".8"/>
      <polygon points="150,170 205,110 205,170" fill="var(--glass)"/>
    </svg>
    <div class="brand" style="top:76px;font-size:13px"><span class="brand__dot"></span>Martial Arts BORQ</div>
  </div>

  <!-- Untere Felder -->
  <div class="pane" style="left:10px;top:190px;width:115px;height:575px">
    <svg class="graphic" viewBox="0 0 115 575" preserveAspectRatio="none">
      <polygon points="0,170 115,60 115,575 0,575" fill="var(--black)"/>
      <polygon points="0,200 115,90 115,104 0,214" fill="var(--red)"/>
      <polygon points="0,430 115,430 115,440 0,440" fill="var(--red)"/>
      <polygon points="0,530 115,530 115,540 0,540" fill="var(--red)"/>
    </svg>
    <div class="photo photo--kick" role="img" aria-label="Foto: Mädchen mit rotem Kopfschutz und pinken Handschuhen beim hohen Kick" style="left:40px;top:270px;width:75px;height:285px"></div>
    <div class="label-kick"><span class="big">KICK</span><span class="small">BOXEN</span></div>
  </div>

  <div class="pane" style="left:135px;top:190px;width:135px;height:575px">
    <svg class="graphic" viewBox="0 0 135 575" preserveAspectRatio="none">
      <polygon points="0,0 135,0 135,200 0,330" fill="var(--black)"/>
      <polygon points="0,330 135,200 135,210 0,342" fill="var(--red)"/>
      <polygon points="60,575 135,500 135,575" fill="var(--black)"/>
    </svg>
    <div class="photo photo--kick" role="img" aria-label="Foto: Bein und pinke Handschuhe der Kickboxerin" style="left:0;top:180px;width:55px;height:120px;border-radius:10px"></div>
    <div class="brand" style="top:70px;font-size:9px;gap:4px"><span class="brand__dot" style="width:7px;height:7px"></span>Martial Arts BORQ</div>
    <div class="rot" style="left:8px;top:555px;font-size:8px;font-weight:700;letter-spacing:.05em;color:#bbb">INFO@MARTIAL-AR</div>
  </div>

  <div class="pane" style="left:280px;top:190px;width:180px;height:575px">
    <svg class="graphic" viewBox="0 0 180 575" preserveAspectRatio="none">
      <polygon points="0,0 180,0 180,20 0,200" fill="var(--black)"/>
      <polygon points="0,260 180,80 180,575 0,575" fill="var(--black)"/>
      <polygon points="0,230 180,50 180,62 0,242" fill="var(--red)"/>
      <polygon points="0,330 180,150 180,156 0,336" fill="var(--coral)"/>
    </svg>
    <div class="photo photo--trick" role="img" aria-label="Foto: Mädchen mit gelbem Gürtel im stehenden Spagat" style="left:25px;top:40px;width:120px;height:510px"></div>
    <div class="rot" style="left:30px;top:500px;transform:rotate(-40deg);font-family:'Alegreya Sans',sans-serif;font-weight:800;font-size:25px">TRICKING</div>
  </div>

  <div class="pane" style="left:470px;top:190px;width:190px;height:575px">
    <svg class="graphic" viewBox="0 0 190 575" preserveAspectRatio="none">
      <polygon points="0,330 190,110 190,360 0,575" fill="var(--black)"/>
      <polygon points="0,180 190,0 190,8 0,188" fill="var(--red)"/>
      <polygon points="110,575 190,500 190,575" fill="var(--black)"/>
    </svg>
    <div class="brand" style="left:40px;right:10px;top:300px;font-size:9px;gap:4px"><span class="brand__dot" style="width:7px;height:7px"></span>Martial Arts BORQ</div>
    <div class="rot contact-phone">0170 / 38 26 91 44</div>
    <div class="rot contact-mail">info@martial-arts-borq.de</div>
  </div>

  <div class="pane" style="left:670px;top:190px;width:190px;height:575px">
    <svg class="graphic" viewBox="0 0 190 575" preserveAspectRatio="none">
      <polygon points="0,0 190,0 190,120 0,300" fill="var(--black)"/>
      <polygon points="0,420 190,250 190,575 0,575" fill="var(--black)"/>
      <polygon points="0,460 190,300 190,314 0,474" fill="var(--red)"/>
      <polygon points="0,535 190,420 190,430 0,545" fill="var(--coral)"/>
    </svg>
    <div class="rot" style="left:22px;top:160px;transform:rotate(-38deg);font-family:'Alegreya Sans',sans-serif;font-weight:800;font-size:24px">JIU JITSU</div>
    <div class="rot" style="left:22px;top:200px;transform:rotate(-38deg);font-weight:700;font-size:16px">Selbstverteitigung</div>
    <div class="photo photo--jiu" role="img" aria-label="Foto: Mädchen im weißen Gi mit gelbem Gürtel in Kampfhaltung" style="left:45px;top:200px;width:115px;height:360px"></div>
  </div>

  <div class="pane" style="left:870px;top:190px;width:205px;height:575px">
    <svg class="graphic" viewBox="0 0 205 575" preserveAspectRatio="none">
      <polygon points="0,10 60,0 0,60" fill="var(--black)"/>
      <polygon points="0,330 205,230 205,575 0,575" fill="var(--black)"/>
      <polygon points="90,300 205,300 205,316 80,316" fill="var(--red)"/>
      <polygon points="70,330 205,330 205,344 60,344" fill="var(--red)"/>
      <polygon points="50,380 205,380 205,395 40,395" fill="var(--coral)"/>
      <g fill="var(--red)">
        <rect x="20" y="430" width="185" height="4"/><rect x="30" y="445" width="175" height="4"/>
        <rect x="40" y="460" width="165" height="4"/><rect x="50" y="475" width="155" height="4"/>
        <rect x="60" y="490" width="145" height="4"/><rect x="70" y="505" width="135" height="4"/>
        <rect x="80" y="520" width="125" height="4"/><rect x="90" y="535" width="115" height="4"/>
      </g>
    </svg>
    <div class="schedule">
      <table>
        <tr><th></th><th>MONTAG</th><th>DIENSTAG</th><th>MITTWOCH</th><th>DONNERSTAG</th><th>FREITAG</th></tr>
        <tr><td class="time">15:00 15:50</td><td>Kick-Boxen 3-5 Jahre</td><td class="jj">Jiu-Jitsu 3-6 Jahre</td><td>Kick-Boxen 3-5 Jahre</td><td class="jj">Jiu-Jitsu 3-6 Jahre</td><td class="empty"></td></tr>
        <tr><td class="time">16:00 16:50</td><td>Kick-Boxen 6-7 Jahre</td><td class="jj">Jiu-Jitsu 7-12 Jahre</td><td>Kick-Boxen 6-7 Jahre</td><td class="jj">Jiu-Jitsu 7-12 Jahre</td><td>Kick-Boxen 3-5 Jahre</td></tr>
        <tr><td class="time">17:00 17:50</td><td>Kick-Boxen 8-10 Jahre</td><td class="alt">Tricking ab 6 Jahre</td><td>Kick-Boxen 8-10 Jahre</td><td class="alt">Tricking ab 6 Jahre</td><td>Kick-Boxen ab 7 Jahre</td></tr>
        <tr><td class="time">18:15 19:15</td><td>Kick-Boxen 10-12 Jahre</td><td class="alt">Kick-Boxen Ü25 Gruppe</td><td>Kick-Boxen 10-12 Jahre</td><td class="alt">Kick-Boxen Ü25 Gruppe</td><td class="empty"></td></tr>
        <tr><td class="time">19:30 21:00</td><td>Kick-Boxen ab 13 Jahre</td><td class="empty"></td><td>Kick-Boxen ab 13 Jahre</td><td class="empty"></td><td class="empty"></td></tr>
      </table>
    </div>
  </div>

</main>
</body>
</html>
```